Bright Harbor Design

We need a web design for our startup company based in Zurich, Switzerland called Bright Harbor. We offer professional flirt and dating advice, self development with seminars and practical coachings.

The final website aims for two capital goals. First, it will contain text, pictures and video based content presenting and advertising our services. Furthermore, we want to bind our costumers with a plattform offering them to share their expiriences related with our services.

The targeted group will be men from 25 to 40 years.
Updates

The design requires also a register-box to put in the clients Name and Email

I need (besides of the "email registration box") a "Video Gallery", "Blog" and "Agenda (with the next events to come)"

Reason: I want to make a poll now

Target Market(s)

Guys around 25 to 40 years who want to improve their social lifestyle

Industry/Entity Type

Advertising

Requirements
Must have
• First and foremost, the design must transfer strong emotions and suggest an attractive social lifestyle.

The design should not be overloaded with content but should include pictures, videos and text.

The design should present a modern, urban lifestyle.
Nice to have
• There is a logo attached to the assignement. However, if you have a good idea for an improved or different logo, please do not hesitate to design your ideas.

```html
<!DOCTYPE html>
<html lang="en">
<head>
<meta charset="utf-8">
<title>Bright Harbor – Dating &amp; Flirting Advice</title>
<link href="https://fonts.googleapis.com/css2?family=PT+Sans:ital,wght@0,400;0,700;1,400&family=PT+Sans+Narrow:wght@400;700&display=swap" rel="stylesheet">
<style>
  :root{
    --navy:#14305f;
    --navy-deep:#0c2148;
    --blue:#1f4a8a;
    --blue-light:#2d5ea3;
    --orange:#f39214;
    --orange-light:#ffab2e;
    --orange-text:#f07f0c;
    --page:#ffffff;
    --ink:#222a33;
    --body:#4a4f56;
    --muted:#6b7078;
    --frame:#e4e6e9;
  }
  *{box-sizing:border-box;margin:0;padding:0}
  html,body{width:849px;height:1200px;overflow:hidden;background:var(--page)}
  body{position:relative;font-family:"PT Sans",Arial,sans-serif;color:var(--body)}
  .abs{position:absolute}

  .topline{left:0;top:0;width:849px;height:4px;background:var(--navy-deep)}
  .header{left:0;top:4px;width:849px;height:110px;background:repeating-linear-gradient(90deg,#f3f4f5 0 3px,#eceef0 3px 5px)}
  .brand{left:40px;top:36px;display:flex;align-items:center;gap:8px;font:700 22px/1 "PT Sans",Arial,sans-serif;color:var(--navy);letter-spacing:.5px}
  .brand-dot{width:26px;height:26px;border-radius:50%;background:var(--navy)}
  .nav{left:284px;top:42px;width:529px;height:40px;background:linear-gradient(var(--orange-light),var(--orange));clip-path:polygon(12px 0,100% 0,100% 100%,0 100%);border-radius:0 4px 4px 0;display:flex;align-items:center;padding-left:30px}
  .nav a{color:#fff;text-decoration:none;font-size:13.5px;padding:0 14px;border-left:1px solid rgba(255,255,255,.35)}
  .nav a:first-child{border-left:none}

  .hero{left:0;top:114px;width:849px;height:301px;background:linear-gradient(180deg,var(--blue-light) 0%,var(--blue) 55%,var(--navy) 100%)}
  .hero-base{left:0;top:375px;width:849px;height:40px;background:var(--navy)}
  .hero-title{left:46px;top:162px;font:700 33px/1 "PT Sans Narrow",Arial,sans-serif;color:#fff}
  .hero-sub{left:47px;top:202px;font:700 16px/1 "PT Sans Narrow",Arial,sans-serif;color:#fff}
  .hero-text{left:47px;top:224px;width:240px;font:italic 11px/17px "PT Sans",Arial,sans-serif;color:#b9c8e0;white-space:nowrap}
  .btn{top:287px;height:27px;border-radius:14px;background:var(--blue-light);box-shadow:inset 0 1px 0 rgba(255,255,255,.2);color:#fff;font:700 11px/27px "PT Sans Narrow",Arial,sans-serif;text-align:center}
  .btn-join{left:44px;width:70px}
  .btn-more{left:119px;width:76px}
  .dots{left:48px;top:344px;display:flex;gap:3px}
  .dots span{width:7px;height:7px;border-radius:50%;background:#fff}
  .hero-photo{left:281px;top:100px;width:535px;height:275px;border:6px solid #fff;border-radius:130px 12px 120px 190px / 150px 12px 60px 140px;background:linear-gradient(100deg,#d9a24a 0%,#f0c46a 18%,#a8743a 32%,#1e1c22 44%,#2a2630 52%,#e8b860 62%,#8a3a4a 74%,#b06a3c 86%,#5a3020 100%)}
  .slider-arrows{left:715px;top:341px;display:flex;gap:6px}

  .service{top:435px;width:245px;height:140px;border:3px solid var(--frame);background:#fff}
  .service-photo{left:13px;top:17px;width:75px;height:85px;border:1px solid #ddd}
  .service-title{left:100px;top:19px;font:700 16px/1 "PT Sans Narrow",Arial,sans-serif;color:var(--orange-text)}
  .service-text{left:101px;top:39px;width:140px;font-size:9.6px;line-height:15.6px;color:var(--body)}
  .service-link{left:101px;top:112px;font:700 9.6px/1 "PT Sans",Arial,sans-serif;color:#333}

  .section-title{font:400 19px/1 "PT Sans",Arial,sans-serif;color:var(--ink)}
  .thumb{width:103px;height:92px;border:1px solid #eee;padding:5px;background:#fff;box-shadow:0 0 2px rgba(0,0,0,.08)}
  .thumb div{width:100%;height:100%}
  .video{left:517px;top:638px;width:293px;height:199px;background:linear-gradient(170deg,#b8c0c8 0%,#8a9098 30%,#6a5a48 55%,#3a2a22 75%,#c0541e 92%,#7a3418 100%)}
  .play{left:642px;top:717px;width:42px;height:42px;border-radius:50%;background:#fff;display:flex;align-items:center;justify-content:center}

  .quote-mark{font:700 26px/1 Georgia,serif;color:#666}
  .t-photo{width:64px;height:58px;border:1px solid #ddd}
  .t-lead{width:125px;font:italic 9.3px/15px "PT Sans",Arial,sans-serif;color:var(--muted)}
  .t-text{width:210px;font:italic 9.3px/15px "PT Sans",Arial,sans-serif;color:var(--muted)}
  .t-author{font:700 9.3px/1 "PT Sans",Arial,sans-serif;color:#444}

  .blog-head{font:400 11.5px/1 "PT Sans",Arial,sans-serif;color:var(--navy)}
  .blog-text{width:300px;font-size:9.3px;line-height:15px;color:var(--body)}

  .footer{left:0;top:1096px;width:849px;height:104px;background:linear-gradient(180deg,var(--navy) 0%,var(--navy-deep) 100%)}
  .footer-nav{left:37px;top:1119px;font:700 9.6px/1 "PT Sans",Arial,sans-serif;color:#fff;word-spacing:1px}
  .footer-copy{left:37px;top:1142px;font-size:9.6px;color:#fff}
  .social{top:1117px;width:17px;height:17px;border-radius:50%;background:#fff}
</style>
</head>
<body>
  <div class="abs topline"></div>
  <header class="abs header"></header>
  <div class="abs brand"><span class="brand-dot"></span>bright harbor</div>
  <nav class="abs nav">
    <a>Main</a><a>About Us</a><a>Services</a><a>Dating</a><a>Video</a><a>Gallery</a><a>Contact</a>
  </nav>

  <section class="abs hero"></section>
  <div class="abs hero-base"></div>
  <h1 class="abs hero-title">Bright Harbor</h1>
  <h2 class="abs hero-sub">Dating &amp; Flirting Advise</h2>
  <p class="abs hero-text">Mauris vel lacus vitae felis vestibulum volutpat.<br>Etiam est nunc, venenatis in, tristique eu,<br>imperdiet ac, nisl.</p>
  <div class="abs btn btn-join">JOIN US</div>
  <div class="abs btn btn-more">READ MORE</div>
  <div class="abs dots"><span></span><span></span><span></span><span></span></div>
  <div class="abs hero-photo" role="img" aria-label="Man and woman chatting in a warmly lit city decor shop"></div>
  <svg class="abs slider-arrows" width="30" height="14" viewBox="0 0 30 14">
    <path d="M10 1 L2 7 L10 13 Z" fill="#fff"/><path d="M18 1 L26 7 L18 13 Z" fill="#fff"/>
  </svg>

  <article class="abs service" style="left:39px">
    <div class="abs service-photo" role="img" aria-label="Smiling woman with a glass of wine at a café" style="background:linear-gradient(135deg,#6a4a34,#c8946e 50%,#dfe6ec)"></div>
    <h3 class="abs service-title">SERVICE HERE</h3>
    <p class="abs service-text">Nunc tempus felis vitae urna. Vivamus porttitor, g, purus nisi eleifend libero, a tempus libero lectus feugiat felis.</p>
    <span class="abs service-link">LEARN MORE</span>
  </article>
  <article class="abs service" style="left:302px">
    <div class="abs service-photo" role="img" aria-label="Man relaxing at home reading a card" style="background:linear-gradient(150deg,#e8e2da,#c0302a 45%,#3a4a6a 75%,#d8d2c8)"></div>
    <h3 class="abs service-title">SERVICE HERE</h3>
    <p class="abs service-text">Nunc tempus felis vitae urna. Vivamus porttitor, g, purus nisi eleifend libero, a tempus libero lectus feugiat felis.</p>
    <span class="abs service-link">LEARN MORE</span>
  </article>
  <article class="abs service" style="left:565px">
    <div class="abs service-photo" role="img" aria-label="Young couple sharing an ice cream outdoors" style="background:linear-gradient(135deg,#3a5a3a,#c89470 45%,#2a2422 80%)"></div>
    <h3 class="abs service-title">SERVICE HERE</h3>
    <p class="abs service-text">Nunc tempus felis vitae urna. Vivamus porttitor, g, purus nisi eleifend libero, a tempus libero lectus feugiat felis.</p>
    <span class="abs service-link">LEARN MORE</span>
  </article>

  <h2 class="abs section-title" style="left:37px;top:610px">Photos Gallery</h2>
  <div class="abs thumb" style="left:37px;top:638px"><div role="img" aria-label="Couple smiling close together" style="background:linear-gradient(135deg,#6a3a22,#d89a76 50%,#f4ece6)"></div></div>
  <div class="abs thumb" style="left:152px;top:638px"><div role="img" aria-label="Couple posing in bright light" style="background:linear-gradient(135deg,#f2eee8,#c49a80 55%,#6a4a3a)"></div></div>
  <div class="abs thumb" style="left:266px;top:638px"><div role="img" aria-label="Couple embracing by the sea" style="background:linear-gradient(135deg,#1a78c8,#d2a07c 55%,#2a1e1a)"></div></div>
  <div class="abs thumb" style="left:380px;top:638px"><div role="img" aria-label="Couple at an evening party" style="background:linear-gradient(135deg,#0e0c0c,#c49274 55%,#1a1616)"></div></div>
  <div class="abs thumb" style="left:39px;top:745px"><div role="img" aria-label="Senior couple smiling" style="background:linear-gradient(135deg,#e6e2dc,#b08a74 55%,#8a7a70)"></div></div>
  <div class="abs thumb" style="left:154px;top:745px"><div role="img" aria-label="Couple laughing under a blue sky" style="background:linear-gradient(135deg,#9cc6ea,#d4a282 55%,#5aa8c8)"></div></div>
  <div class="abs thumb" style="left:268px;top:745px"><div role="img" aria-label="Elegant couple in evening wear" style="background:linear-gradient(135deg,#121010,#c8a088 55%,#0e0c0c)"></div></div>
  <div class="abs thumb" style="left:382px;top:745px"><div role="img" aria-label="Playful couple in the city" style="background:linear-gradient(135deg,#6a4a3a,#d0a890 50%,#2a4a7a)"></div></div>

  <h2 class="abs section-title" style="left:517px;top:610px">Watch Our Video</h2>
  <div class="abs video" role="img" aria-label="Video still of a young couple sitting together on a city street"></div>
  <div class="abs play"><svg width="16" height="18" viewBox="0 0 16 18"><path d="M3 1 L15 9 L3 17 Z" fill="#1b1b1b"/></svg></div>

  <h2 class="abs section-title" style="left:40px;top:878px">Testimonials</h2>
  <span class="abs quote-mark" style="left:38px;top:909px">&ldquo;</span>
  <div class="abs t-photo" style="left:60px;top:910px;background:linear-gradient(135deg,#e6e6e6,#9a6446 55%,#3a2a22)" role="img" aria-label="Portrait of a smiling man"></div>
  <p class="abs t-lead" style="left:134px;top:905px">Nunc tempus felis vitae urna. Vivamus porttitor, neque at volutpat rutrum, purus nisi eleifend libero, a tempus libero</p>
  <p class="abs t-text" style="left:58px;top:972px">Morbi eget arcu. Morbi porta, libero id ullamcorper nonummy, nibh ligula pulvinar metus, eget consec-<br>tetuer augue nisi quis quis lacus. <b style="font-style:normal">&rdquo;</b></p>
  <span class="abs t-author" style="left:59px;top:1027px">By Author Name</span>

  <span class="abs quote-mark" style="left:268px;top:909px">&ldquo;</span>
  <div class="abs t-photo" style="left:291px;top:910px;background:linear-gradient(135deg,#c8a478,#3a2018 55%,#1a100c)" role="img" aria-label="Portrait of a woman with dark curly hair"></div>
  <p class="abs t-lead" style="left:364px;top:905px">Nunc tempus felis vitae urna. Vivamus porttitor, neque at volutpat rutrum, purus nisi eleifend libero, a tempus libero</p>
  <p class="abs t-text" style="left:288px;top:972px">Morbi eget arcu. Morbi porta, libero id ullamcorper nonummy, nibh ligula pulvinar metus, eget consec-<br>tetuer augue nisi quis quis lacus. <b style="font-style:normal">&rdquo;</b></p>
  <span class="abs t-author" style="left:289px;top:1027px">By Author Name</span>

  <h2 class="abs section-title" style="left:516px;top:879px">Recent Blog Post</h2>
  <h3 class="abs blog-head" style="left:518px;top:909px">Nunc tempus felis vitae urna.</h3>
  <p class="abs blog-text" style="left:518px;top:926px">Curabitur vel mi sit amet magna malesuada ultrices. Ut nisi erat, fermen-<br>tum vel, congue id, euismod in, elit. Fusce ultricies, orci ac</p>
  <h3 class="abs blog-head" style="left:520px;top:979px">Duis tincidunt lectus quis dui viverra</h3>
  <p class="abs blog-text" style="left:520px;top:996px">Phasellus felis dolor, scelerisque a, tempus eget, lobortis id, libero. Donec scelerisque leo ac risus. Praesent sit amet est. In dictum, dolor eu dictum porttitor, enim felis viverra mi, eget luctus massa purus quis odio.</p>

  <footer class="abs footer"></footer>
  <div class="abs footer-nav">MAIN &nbsp;| &nbsp;ABOUT US &nbsp;| &nbsp;SERVICES &nbsp;| &nbsp;DATING &nbsp;| &nbsp;VIDEO &nbsp;| &nbsp;GALLERY &nbsp;| &nbsp;CONTACT</div>
  <div class="abs footer-copy">© 2013 Company Name. &nbsp;All right reserved. &nbsp;Term of Use</div>
  <span class="abs social" style="left:742px"></span>
  <span class="abs social" style="left:762px"></span>
  <span class="abs social" style="left:782px"></span>
</body>
</html>
```